Anesthesia Medical Practice Business Card

We need a business card to hand out to surgeons with my basic information. Something that stands out but is not over the top. The medical community is rather conservative. I'd like them to call me first when flipping through their rolodex of anesthesiologists. I'd like the card to communicate confidence, control, professionalism yet serenity. I don't want the card to be pricey to print.

he logo will be provided as a vector graphic in addition to a complete business card design including the logo

Lem Varo Keshtel, M.D.
Board Certified Anesthesiologist

(555) 386-2157

lkeshtel@quorvanmail.example

Mailing Address:
47315 Brindlecove Ave.
Suite 382-6475
Los Angeles, CA 90877

A logo that inegrates my initials perhaps
LK MD
My initials are LK and MD as in Medical Doctor

or
perhaps a physician in surgical mask and cap caring for a patient

Target Market(s)

Surgeons who need anesthesia services

Industry/Entity Type

Medical

Requirements
Must have
• the logo will be provided as a vector graphic in addition to a complete business card design including the logo

Lem Varo Keshtel, M.D.

(555) 386-2157

lkeshtel@quorvanmail.example

Mailing Address:
47315 Brindlecove Ave.
Suite 382-6475
Los Angeles, CA 90877

Nice to have
• A logo that inegrates my initials perhaps
LK MD

or

```html
<!DOCTYPE html>
<html lang="en">
<head>
<meta charset="utf-8">
<title>Lem Varo Keshtel, M.D. – Business Card</title>
<link rel="stylesheet" href="https://fonts.googleapis.com/css2?family=Montserrat:wght@400;500;700;800&display=swap">
<style>
  :root {
    --bg: #c9cacc;
    --teal: #5bc1c5;
    --teal-deep: #3fb0b6;
    --white: #ffffff;
    --paper: #fbfbfb;
    --ink: #5f6566;
    --rule: #b9bdbe;
  }
  * { margin: 0; padding: 0; box-sizing: border-box; }
  html, body { width: 1200px; height: 900px; overflow: hidden; }
  body {
    background: var(--bg);
    font-family: "Montserrat", Arial, sans-serif;
    display: flex;
    flex-direction: column;
    align-items: center;
    justify-content: center;
    gap: 44px;
  }
  .card {
    width: 630px;
    height: 360px;
    border-radius: 30px;
    position: relative;
    overflow: hidden;
    box-shadow: 0 6px 18px rgba(0,0,0,0.15);
  }

  /* Front */
  .card-front { background: var(--teal); }
  .front-wordmark {
    position: absolute;
    left: 0; right: 0;
    top: 100px;
    display: flex;
    align-items: center;
    justify-content: center;
    gap: 16px;
  }
  .front-initials {
    color: var(--white);
    font-weight: 800;
    font-size: 92px;
    letter-spacing: 2px;
    line-height: 1;
  }
  .front-dot {
    width: 20px;
    height: 20px;
    border-radius: 50%;
    background: var(--white);
  }
  .front-name {
    position: absolute;
    left: 0; right: 0;
    top: 236px;
    text-align: center;
    color: var(--white);
    font-weight: 800;
    font-size: 30px;
    letter-spacing: 0.5px;
  }

  /* Back */
  .card-back { background: var(--paper); }
  .back-wordmark {
    position: absolute;
    left: 70px;
    top: 144px;
    width: 190px;
    display: flex;
    align-items: center;
    justify-content: center;
    gap: 12px;
  }
  .back-initials {
    color: var(--ink);
    font-weight: 800;
    font-size: 64px;
    letter-spacing: 1px;
    line-height: 1;
  }
  .back-dot {
    width: 16px;
    height: 16px;
    border-radius: 50%;
    background: var(--teal);
  }
  .back-details {
    position: absolute;
    left: 300px;
    top: 70px;
    padding-left: 22px;
    border-left: 1.5px solid var(--rule);
    height: 220px;
    color: var(--ink);
    font-size: 15px;
    line-height: 1.3;
  }
  .back-name { color: var(--teal-deep); font-size: 20px; font-weight: 500; }
  .back-title { font-size: 14px; margin-bottom: 16px; }
  .contact-row { display: flex; align-items: center; gap: 10px; }
  .contact-row svg { width: 13px; height: 13px; flex: none; }
  .address-label { color: var(--teal-deep); margin-top: 14px; padding-left: 23px; }
  .address-lines { padding-left: 23px; }
</style>
</head>
<body>
  <section class="card card-front" aria-label="Card front">
    <div class="front-wordmark">
      <span class="front-initials">LK</span>
      <span class="front-dot" aria-hidden="true"></span>
    </div>
    <div class="front-name">Lem Varo Keshtel, M.D.</div>
  </section>

  <section class="card card-back" aria-label="Card back">
    <div class="back-wordmark">
      <span class="back-initials">LK</span>
      <span class="back-dot" aria-hidden="true"></span>
    </div>
    <div class="back-details">
      <div class="back-name">Lem Varo Keshtel, M.D.</div>
      <div class="back-title">Board Certified Anesthesiologist</div>
      <div class="contact-row">
        <svg viewBox="0 0 13 13" aria-hidden="true"><rect width="13" height="13" rx="2" fill="var(--teal)"/><path d="M4 3h2l.6 2-1 .8a5 5 0 0 0 1.6 1.6l.8-1 2 .6v2a1 1 0 0 1-1 1A6 6 0 0 1 3 4a1 1 0 0 1 1-1z" fill="var(--white)"/></svg>
        <span>(555) 386-2157</span>
      </div>
      <div class="contact-row">
        <svg viewBox="0 0 13 13" aria-hidden="true"><rect width="13" height="13" rx="2" fill="var(--teal)"/><rect x="2.5" y="4" width="8" height="5.5" fill="none" stroke="var(--white)" stroke-width="1"/><path d="M2.5 4l4 3 4-3" fill="none" stroke="var(--white)" stroke-width="1"/></svg>
        <span>lkeshtel@quorvanmail.example</span>
      </div>
      <div class="address-label">Mailing Address:</div>
      <div class="address-lines">
        47315 Brindlecove Ave.<br>
        Suite 382-6475<br>
        Los Angeles, CA 90877
      </div>
    </div>
  </section>
</body>
</html>
```